Suds Haven Laundromat Wordpress Design

We need a Wordpress website design for our laundromat, Suds Haven Atlanta, at www.sudshavenatlanta-example.com. We would like to have 6 pages: Home, About Us, Services, Locations, Reviews and Contact us. We will provide content for the text on each page. What we do: We are a full service laundromat that provides dry cleaning drop off, professional laundry services, wash dry fold and self service laundry to the local community. We would like to use the color scheme from our logo to convey a warm, safe, and bright business that caters to its diverse community.
Updates

I like the structure of this laundromat website: http://www.washtroveusa-example.com/ Using my logo and color scheme in the above referenced website is what. Am looking for. The photos attached to the project with the female model should be used as a primary focus and supplemented by actual photos of the equipment.

Target Market(s)

Our target market is a diverse group of people from Midtown Atlanta - LGBTQ community /Locals/Regulars that have been coming to laundromat for 30 years.

Industry/Entity Type

Laundromat

Coding

Coded - Design and coding required

Number of Pages Required

5+ page

Font styles to use
Sans Serif

Colors
0054AA
0677BA
7BADD7
CADEEF
E8F1F8

Requirements
Must have
• Feature this video on the main page: https://videohost-example.com/xq7Rm2bPz4k

```html
<!DOCTYPE html>
<html lang="en">
<head>
<meta charset="utf-8">
<title>Reviews – Suds Haven Atlanta</title>
<link rel="stylesheet" href="https://fonts.googleapis.com/css2?family=Montserrat:wght@400;500;600&family=Oswald:wght@500&family=Questrial&display=swap">
<style>
  :root {
    --brand-blue: #0054AA;
    --brand-mid: #0677BA;
    --brand-sky: #1E9BD7;
    --brand-light: #CADEEF;
    --brand-pale: #E8F1F8;
    --ink: #1d1d1d;
    --body-text: #333333;
    --footer-bg: #2E4467;
    --footer-line: #4A5F80;
    --white: #ffffff;
  }
  * { margin: 0; padding: 0; box-sizing: border-box; }
  html, body { width: 770px; height: 1200px; overflow: hidden; background: var(--white); }
  body { position: relative; font-family: "Questrial", sans-serif; color: var(--body-text); }

  .site-header { position: absolute; top: 0; left: 0; width: 770px; height: 48px; background: var(--white); z-index: 3; }
  .brand { position: absolute; left: 66px; top: 13px; display: flex; align-items: center; gap: 6px; }
  .brand-dot { width: 12px; height: 12px; border-radius: 50%; background: var(--brand-sky); }
  .brand-name { font-family: "Montserrat", sans-serif; font-weight: 600; font-size: 15px; color: var(--brand-blue); letter-spacing: 0.2px; }
  .main-nav { position: absolute; top: 21px; left: 349px; display: flex; gap: 0; font-family: "Montserrat", sans-serif; font-size: 8.3px; color: var(--ink); }
  .main-nav a { position: absolute; white-space: nowrap; color: inherit; text-decoration: none; }
  .main-nav .is-active { font-weight: 600; }
  .nav-underline { position: absolute; left: 530px; top: 46px; width: 39px; height: 2.5px; background: var(--brand-blue); }
  .header-divider { position: absolute; left: 660px; top: 12px; width: 1px; height: 24px; background: var(--brand-blue); }
  .header-social { position: absolute; top: 20px; width: 8px; height: 8px; border-radius: 50%; background: var(--ink); }

  .hero { position: absolute; top: 48px; left: 0; width: 770px; height: 390px; }
  .hero-photo { position: absolute; inset: 0; background: linear-gradient(180deg, #BFDCD6 0%, #D8E4DE 40%, #B9B5AA 75%, #8F8E8A 100%); }
  .hero-curve { position: absolute; top: 0; left: 0; }

  .breadcrumb { position: absolute; top: 446px; left: 104px; font-family: "Montserrat", sans-serif; font-size: 8px; color: var(--ink); }
  .breadcrumb .current { color: var(--brand-blue); font-weight: 500; }

  .section-title { position: absolute; top: 505px; left: 0; width: 770px; text-align: center; font-family: "Oswald", sans-serif; font-weight: 500; font-size: 20px; letter-spacing: -0.3px; color: #2a2a2a; }
  .section-title span { color: var(--brand-blue); }
  .title-rule { position: absolute; top: 534px; left: 370px; width: 29px; height: 1.5px; background: var(--brand-sky); }

  .testimonial { position: absolute; top: 587px; width: 178px; height: 218px; background: var(--white); box-shadow: 0 6px 10px rgba(0,0,0,0.08); text-align: center; }
  .quote-badge { position: absolute; top: -27px; left: 59px; width: 60px; height: 60px; border-radius: 50%; background: var(--white); box-shadow: 0 1px 3px rgba(0,0,0,0.12); }
  .quote-badge::after { content: ""; position: absolute; top: 3px; left: 3px; width: 54px; height: 54px; border-radius: 50%; background: var(--brand-blue); }
  .quote-badge svg { position: absolute; top: 19px; left: 20px; z-index: 1; }
  .reviewer { position: absolute; top: 45px; left: 0; width: 100%; font-family: "Montserrat", sans-serif; font-weight: 500; font-size: 10.4px; color: var(--brand-blue); }
  .review-text { position: absolute; top: 64px; left: 8px; right: 8px; font-size: 7.7px; line-height: 15.7px; color: var(--body-text); }

  .site-footer { position: absolute; top: 862px; left: 0; width: 770px; height: 338px; background: var(--footer-bg); color: var(--white); }
  .footer-brand { position: absolute; top: 58px; left: 0; width: 770px; display: flex; justify-content: center; align-items: center; gap: 8px; }
  .footer-brand .brand-dot { width: 16px; height: 16px; background: var(--white); }
  .footer-brand .brand-name { color: var(--white); font-size: 24px; font-weight: 600; }
  .footer-rule { position: absolute; height: 1px; background: var(--footer-line); }
  .footer-nav { position: absolute; top: 147px; font-family: "Montserrat", sans-serif; font-size: 9.8px; }
  .footer-nav a { position: absolute; white-space: nowrap; color: var(--white); text-decoration: none; }
  .footer-social { position: absolute; top: 144px; width: 19px; height: 19px; border-radius: 50%; background: var(--white); }
  .footer-social.alt { background: var(--brand-sky); box-shadow: 0 0 0 1.5px var(--white); }
  .contact { position: absolute; font-family: "Montserrat", sans-serif; font-size: 8.8px; line-height: 15.5px; color: var(--white); }
  .contact-icon { position: absolute; }
  .delivery { color: var(--brand-sky); }
  .delivery strong { font-weight: 600; }
  .copyright { position: absolute; top: 296px; left: 0; width: 770px; text-align: center; font-family: "Montserrat", sans-serif; font-size: 7.8px; color: #e4e8ef; }
  .copyright strong { font-weight: 600; color: var(--white); }
</style>
</head>
<body>

<header class="site-header">
  <div class="brand"><span class="brand-dot"></span><span class="brand-name">The Suds Haven</span></div>
  <nav class="main-nav">
    <a style="left:0">HOME</a>
    <a style="left:49px">ABOUT US</a>
    <a style="left:117px">SERVICES</a>
    <a class="is-active" style="left:182px">REVIEWS</a>
    <a style="left:245px">CONTACT US</a>
  </nav>
  <div class="nav-underline"></div>
  <div class="header-divider"></div>
  <span class="header-social" style="left:672px"></span>
  <span class="header-social" style="left:689px"></span>
</header>

<section class="hero">
  <div class="hero-photo" role="img" aria-label="Photograph of a woman in a blue dress walking between rows of front-loading washers in a retro laundromat with a wall clock and script signage"></div>
  <svg class="hero-curve" width="770" height="390" viewBox="0 0 770 390" aria-hidden="true">
    <path d="M0 330 Q385 420 770 330 L770 390 L0 390 Z" fill="#ffffff"/>
    <path d="M0 340 Q385 410 738 345 Q385 430 0 346 Z" fill="#0054AA"/>
  </svg>
</section>

<div class="breadcrumb">HOME / <span class="current">REVIEWS</span></div>

<h1 class="section-title">CUSTOMER <span>TESTIMONIALS</span></h1>
<div class="title-rule"></div>

<article class="testimonial" style="left:103px">
  <div class="quote-badge"><svg width="20" height="16" viewBox="0 0 20 16"><path d="M1 1h7v7l-3 7H2l2-6H1z M11 1h7v7l-3 7h-3l2-6h-3z" fill="#7BADD7"/></svg></div>
  <h2 class="reviewer">Marisa Kettleby</h2>
  <p class="review-text">Great drop off laundry location to have professionals do your laundry. They are quick, honor requests about how to bag it up, and are friendly and reasonable. They are also opened 7 days a week and have coin service, folding tables and a comfortable waiting area while you do your own.</p>
</article>

<article class="testimonial" style="left:296px">
  <div class="quote-badge"><svg width="20" height="16" viewBox="0 0 20 16"><path d="M1 1h7v7l-3 7H2l2-6H1z M11 1h7v7l-3 7h-3l2-6h-3z" fill="#7BADD7"/></svg></div>
  <h2 class="reviewer">Desmond Quill</h2>
  <p class="review-text">Great customer service, friendly staff, the place looks clean &amp; they have the option to pay with your phone &amp; coins, great acco- mmodating to the customers. Thank you!</p>
</article>

<article class="testimonial" style="left:488px">
  <div class="quote-badge"><svg width="20" height="16" viewBox="0 0 20 16"><path d="M1 1h7v7l-3 7H2l2-6H1z M11 1h7v7l-3 7h-3l2-6h-3z" fill="#7BADD7"/></svg></div>
  <h2 class="reviewer">Tobias Renwick</h2>
  <p class="review-text">This is one of the cleanest and friendly Coin Laundromats I've ever been too. Great place!</p>
</article>

<footer class="site-footer">
  <div class="footer-brand"><span class="brand-dot"></span><span class="brand-name">THE SUDS HAVEN</span></div>
  <div class="footer-rule" style="top:128px;left:195px;width:380px"></div>
  <nav class="footer-nav">
    <a style="left:199px">Home</a>
    <a style="left:250px">About Us</a>
    <a style="left:317px">Services</a>
    <a style="left:385px">Reviews</a>
    <a style="left:448px">Contact Us</a>
  </nav>
  <span class="footer-social" style="left:523px"></span>
  <span class="footer-social alt" style="left:552px"></span>
  <div class="footer-rule" style="top:180px;left:210px;width:350px"></div>

  <svg class="contact-icon" style="left:157px;top:204px" width="12" height="14" viewBox="0 0 12 14" aria-hidden="true"><path d="M6 1a4 4 0 0 1 4 4c0 3-4 8-4 8S2 8 2 5a4 4 0 0 1 4-4z" fill="none" stroke="#fff" stroke-width="0.9"/><circle cx="6" cy="5" r="1.4" fill="none" stroke="#fff" stroke-width="0.9"/></svg>
  <p class="contact" style="left:178px;top:206px">Brightwater Plaza Shopping Center, 2870 Maple<br>Crest Ave NE., # 212, Atlanta, GA 30399</p>
  <svg class="contact-icon" style="left:157px;top:244px" width="12" height="12" viewBox="0 0 12 12" aria-hidden="true"><path d="M2.5 1.2l2 2.2-1 1.4c.8 1.6 2 2.8 3.6 3.6l1.4-1 2.2 2-1.2 1.6C5 10.6 1.4 7 .9 2.4z" fill="none" stroke="#fff" stroke-width="0.9"/></svg>
  <p class="contact" style="left:177px;top:240px">(404) 555-0148</p>

  <p class="contact delivery" style="left:392px;top:205px"><strong>Delivery Available*</strong> please contact us for details</p>
  <p class="contact" style="left:392px;top:226px">Covid 19 hours – open 7 days a week 8 am to 8 pm<br>Last wash begins 6:30 pm</p>

  <div class="footer-rule" style="top:267px;left:103px;width:564px"></div>
  <p class="copyright">Copyright © 2021 <strong>Suds Haven Atlanta</strong>. All Rights Reserved.</p>
</footer>

</body>
</html>
```